Electronic Repair Company need a new flyer!

Hi Guys,

I need a new flyer for my repair company that I can use for my door 2 door marketing. The flyers will be send to thousands of addresses in the Netherlands. You can design the flyer in English but I need to be able to translate the flyer into Dutch, so I might need the PSD file.

We repair Computers, Laptops and ALL Zelto devices.

For some inspiration please take a look at: www.bravolmend.nl

And see the pictures below ;)

Target Market(s)

Computer & Smartphone Repair

Industry/Entity Type

Electronic

Requirements
Nice to have
• I would like to have some pictures from our staff (like on our website) in it so people can see who we really are :)

```html
<!DOCTYPE html>
<html lang="en">
<head>
<meta charset="utf-8">
<title>Bravolmend repair flyer</title>
<link href="https://fonts.googleapis.com/css2?family=Archivo+Black&family=Oswald:wght@500;700&family=Roboto+Condensed:wght@400;700&display=swap" rel="stylesheet">
<style>
  :root{
    --red:#e8432e;
    --ink:#2b2b2b;
    --paper:#ffffff;
    --stage:#e6e6e6;
    --photo-a:#cfd6dc;
  }
  *{box-sizing:border-box;margin:0;padding:0}
  html,body{width:1200px;height:1200px;overflow:hidden;background:var(--stage)}
  body{font-family:"Roboto Condensed",Arial,sans-serif}
  .flyer{position:absolute;left:190px;top:20px;width:820px;height:1160px;background:var(--paper);overflow:hidden;box-shadow:0 6px 24px rgba(0,0,0,.18)}
  .flyer-bg{position:absolute;inset:0}
  .abs{position:absolute}
  .brand-tag{right:30px;top:18px;font-weight:700;font-size:22px;color:var(--paper);background:var(--red);padding:2px 10px}
  .badge{left:60px;top:240px;width:220px;height:220px;border-radius:50%;background:var(--ink);border:10px solid var(--red);box-shadow:0 0 0 6px #fff,0 6px 14px rgba(0,0,0,.3);color:#fff;text-align:center;padding-top:46px}
  .badge-small{font-size:30px;line-height:1}
  .badge-big{font-family:"Oswald",sans-serif;font-weight:700;font-size:74px;line-height:1.05}
  .headline{left:30px;top:478px;width:550px;font-family:"Archivo Black",sans-serif;line-height:.95;white-space:nowrap}
  .headline-1{color:var(--red);font-size:88px}
  .headline-2{color:var(--ink);font-size:50px}
  .headline-3{color:var(--ink);font-size:30px;margin-top:6px}
  .tagline-band{left:0;top:668px;width:580px;height:54px;background:var(--ink);color:#fff;font-family:"Archivo Black",sans-serif;font-size:28px;letter-spacing:1px;padding:9px 0 0 30px;white-space:nowrap}
  .intro{left:30px;top:732px;width:540px;color:var(--red);font-size:17px;line-height:1.25}
  .services{left:592px;top:348px;width:212px}
  .services-title{display:inline-block;margin-left:24px;background:var(--ink);color:#fff;font-weight:700;font-size:24px;padding:4px 16px;border-radius:16px 16px 0 0}
  .service{display:flex;align-items:center;gap:12px;height:60px;background:var(--red);border-bottom:2px solid var(--paper);padding-left:14px;color:#fff}
  .service:first-of-type{border-radius:8px 0 0 0}
  .service:last-child{border-radius:0 0 8px 8px;border-bottom:none}
  .service-icon{width:30px;height:30px;flex:none}
  .service-name{font-weight:700;font-size:24px;line-height:1}
  .service-sub{font-weight:700;font-size:14px;line-height:1}
  .lower-photo{left:0;top:800px;width:820px;height:295px;background:linear-gradient(120deg,#e9eef2 0%,var(--photo-a) 55%,#b9c4cc 100%)}
  .contact{left:400px;top:805px;width:404px;display:flex;flex-direction:column}
  .info{background:var(--ink);color:#fff;border-radius:10px 0 0 0;padding-bottom:8px}
  .info-head{background:var(--red);font-weight:700;font-size:21px;padding:6px 14px;border-radius:10px 0 0 0}
  .info-text{font-size:15px;padding:6px 14px 0;line-height:1.2}
  .info-call{text-align:center;font-size:20px;margin-top:4px}
  .info-phone{text-align:center;font-family:"Oswald",sans-serif;font-weight:500;font-size:52px;line-height:1.05}
  .info-web{text-align:center;font-size:20px;font-weight:700;border-top:1px solid #888;margin:2px 20px 0;padding-top:2px;line-height:1.2}
  .location{background:var(--red);color:#fff;border-radius:12px 0 0 12px;display:flex;align-items:center;gap:10px;padding:8px 12px;font-size:16px;line-height:1.15;margin-left:-20px}
  .location svg{flex:none}
  .brands{left:0;top:1098px;width:820px;height:62px;background:var(--red);display:flex;justify-content:space-around;align-items:center;color:#fff;font-weight:700;font-size:20px;letter-spacing:1px}
</style>
</head>
<body>
<div class="flyer">
  <svg class="flyer-bg" width="820" height="1160" viewBox="0 0 820 1160">
    <defs>
      <linearGradient id="peachFade" x1="0" y1="0" x2="1" y2="1">
        <stop offset="0" stop-color="#f3b79b"/>
        <stop offset="1" stop-color="#fff3ea"/>
      </linearGradient>
      <linearGradient id="shopPhoto" x1="0" y1="0" x2="1" y2="1">
        <stop offset="0" stop-color="#7d8790"/>
        <stop offset=".5" stop-color="#cfd4d8"/>
        <stop offset="1" stop-color="#eef0f1"/>
      </linearGradient>
    </defs>
    <rect width="820" height="660" fill="url(#peachFade)"/>
    <path d="M0,470 C250,410 520,380 820,360 V660 H0 Z" fill="#fff"/>
    <path d="M90,0 H820 V330 C620,345 420,370 250,430 C200,290 140,140 90,0 Z" fill="#333"/>
    <path d="M100,0 H820 V320 C620,335 420,358 255,418 C205,280 150,135 100,0 Z" fill="url(#shopPhoto)" role="img" aria-label="Photo of the repair shop counter with two staff members helping a customer"/>
    <path d="M255,418 C420,358 620,335 820,320" fill="none" stroke="var(--red)" stroke-width="8"/>
    <path d="M0,40 C40,150 70,260 90,320" fill="none" stroke="var(--red)" stroke-width="6"/>
  </svg>

  <div class="abs brand-tag">BRAVOLMEND.NL</div>

  <div class="abs badge">
    <div class="badge-small">repair with</div>
    <div class="badge-big">24 hr!</div>
  </div>

  <div class="abs headline">
    <div class="headline-1">QUICKLY</div>
    <div class="headline-2">QUALITATIVELY</div>
    <div class="headline-3">AND ON A NO WIN NO FEE!</div>
  </div>

  <div class="abs tagline-band">Pleasant, we Bravolmend.nl</div>

  <p class="abs intro">More than 20 technicians are six days a week, ready to repair your device as soon as possible. Because we have more than 1.2 million parts center in stock, we can often fix within 24 hours of your device!</p>

  <div class="abs services">
    <div class="services-title">Our Service</div>
    <div class="service">
      <svg class="service-icon" viewBox="0 0 30 30"><rect x="1" y="1" width="28" height="28" rx="4" fill="#fff"/><circle cx="15" cy="15" r="7" fill="var(--ink)"/></svg>
      <div><div class="service-name">ZELTO</div><div class="service-sub">REPAIR</div></div>
    </div>
    <div class="service">
      <svg class="service-icon" viewBox="0 0 30 30"><rect x="1" y="1" width="28" height="28" rx="4" fill="#fff"/><rect x="6" y="7" width="18" height="12" fill="var(--ink)"/><rect x="12" y="20" width="6" height="4" fill="var(--ink)"/></svg>
      <div><div class="service-name">COMPUTER</div><div class="service-sub">REPAIR</div></div>
    </div>
    <div class="service">
      <svg class="service-icon" viewBox="0 0 30 30"><rect x="1" y="1" width="28" height="28" rx="4" fill="#fff"/><rect x="8" y="8" width="14" height="10" fill="var(--ink)"/><rect x="5" y="19" width="20" height="3" fill="var(--ink)"/></svg>
      <div><div class="service-name">LAPTOP</div><div class="service-sub">REPAIR</div></div>
    </div>
    <div class="service">
      <svg class="service-icon" viewBox="0 0 30 30"><rect x="1" y="1" width="28" height="28" rx="4" fill="#fff"/><rect x="8" y="5" width="14" height="20" rx="2" fill="var(--ink)"/><rect x="10" y="7" width="10" height="15" fill="#fff"/></svg>
      <div><div class="service-name">TABLET</div><div class="service-sub">REPAIR</div></div>
    </div>
    <div class="service">
      <svg class="service-icon" viewBox="0 0 30 30"><rect x="1" y="1" width="28" height="28" rx="4" fill="#fff"/><rect x="10" y="5" width="10" height="20" rx="2" fill="var(--ink)"/></svg>
      <div><div class="service-name">SMARTPHONE</div><div class="service-sub">REPAIR</div></div>
    </div>
  </div>

  <div class="abs lower-photo" role="img" aria-label="Photo of a smiling technician holding an open laptop and a charger, over a blurred keyboard background"></div>

  <div class="abs contact">
    <div class="info">
      <div class="info-head">We repair your social and business life!</div>
      <p class="info-text">With us you can go for the repair of your Zelto Desk or Zelto Book. Zelto help our specialists will be happy with a professional</p>
      <div class="info-call">Call our customer service</div>
      <div class="info-phone">088-0123456</div>
      <div class="info-web">www.bravolmend.nl</div>
    </div>
    <div class="location">
      <svg width="26" height="34" viewBox="0 0 26 34"><path d="M13,1 C6,1 1,6 1,13 C1,22 13,33 13,33 C13,33 25,22 25,13 C25,6 20,1 13,1 Z" fill="#fff"/><circle cx="13" cy="13" r="5" fill="var(--red)"/></svg>
      <span>Opening soon Hoorn and Delft Lindenstraat 52,<br>Amsterdam | Molenweg 18, Nieuw-Vennep</span>
    </div>
  </div>

  <div class="abs brands">
    <span>NORVEX</span><span>KALTO</span><span>VIMORA</span><span>TESSIN</span><span>ORBIQ</span><span>LUMETRA</span><span>QUELL</span><span>DAXON</span><span>FERRO</span>
  </div>
</div>
</body>
</html>
```